Product Design for VelaMira

Design Brief for VelaMira Product Packaging

Objective:
Create a cohesive, elegant, and brand-consistent packaging design for the VelaMira product line. The signature visual theme should reflect luxury, femininity, and clean beauty values.

---

🎨 Core Design Direction

Unified Aesthetic: All containers must prominently feature the floral pattern shown in "Pattern Reference: Image 3". This design serves as the brand's signature aesthetic and must be applied uniformly across all SKUs.

Brand Logo Placement: The VelaMira logo (provided) should be clearly visible and harmoniously integrated into the patterned background.

Color Palette: Base colors should complement the brand’s primary palette: black, blush pink, and white.

---

🧴 Product-Specific Packaging Specifications

1. Mascara

Bottle Type: Sleek mascara tube with a wand applicator

Capacity: 5ml

Design: Use floral pattern from Pattern Reference Image 3. Ensure the pattern does not obstruct the readability of the logo or any regulatory text.

2. Eyebrow Growth Serum

Bottle Type: 5ml tube with fine-tip brush applicator

Capacity: 5ml

Design: Same floral pattern, scaled and applied proportionally to match the mascara for consistency

3. Eyelash Growth Serum

Bottle Type: 5ml tube with fine-tip brush (similar to the eyebrow serum, unless otherwise advised)

Capacity: 5ml

Design: Identical styling to maintain unity across lash & brow products

4. Anti-Aging Serum or Lotion

Bottle Type: 30ml airless pump bottle (preferred for hygiene and product stability)

Capacity: 30ml

Design: Apply floral pattern from Pattern Reference and scale appropriately for larger surface area

5. Hair Growth Spray

Bottle Type: 50ml fine mist spray bottle

Capacity: 50ml

Design: Pattern applied and scaled for taller profile; maintain visual harmony with skincare line

---

📦 Additional Notes

Please ensure packaging aligns with clean beauty standards (no overly glossy plastic finishes, avoid excessive secondary packaging unless sustainable).

Materials should be eco-conscious where possible.

If embossing, foil stamping, or UV finishing is available for logo accents, please suggest options.

```html
<!DOCTYPE html>
<html lang="en">
<head>
<meta charset="utf-8">
<title>VelaMira Eyebrow Growth Serum Packaging</title>
<link rel="stylesheet" href="https://fonts.googleapis.com/css2?family=Poppins:wght@400;500&display=swap">
<style>
  :root {
    --page: #ffffff;
    --ink: #1e1e1e;
    --blush: #f6d3cc;
    --blush-soft: #fbeae6;
    --floral-tone: #f3ddd7;
    --floral-light: #fdf6f4;
    --gold-dark: #b07a1c;
    --gold-light: #f6e27a;
    --cap: #1a1a1a;
    --tube-white: #f4f3f3;
  }
  * { box-sizing: border-box; margin: 0; padding: 0; }
  html, body {
    width: 809px;
    height: 1200px;
    overflow: hidden;
    background: var(--page);
    font-family: "Poppins", sans-serif;
    color: var(--ink);
  }
  .canvas { position: relative; width: 809px; height: 1200px; }

  .carton {
    position: absolute;
    left: 102px; top: 103px;
    width: 378px; height: 993px;
    overflow: hidden;
  }
  .tube {
    position: absolute;
    left: 570px; top: 106px;
    width: 136px; height: 985px;
    overflow: hidden;
  }
  .tube-cap {
    position: absolute;
    left: 0; top: 0;
    width: 100%; height: 296px;
    background: var(--cap);
    border-radius: 6px 6px 0 0;
  }

  .floral-field {
    position: absolute;
    left: 0; width: 100%;
    background: linear-gradient(160deg, var(--floral-light) 0%, var(--floral-tone) 50%, var(--floral-light) 100%);
  }
  .carton .floral-field { top: 0; height: 267px; }
  .tube .floral-field { top: 296px; height: 186px; }

  .gold-band {
    position: absolute;
    left: 0; width: 100%;
    height: 4px;
    background: linear-gradient(90deg, var(--gold-dark), var(--gold-light) 55%, var(--gold-dark));
  }
  .carton .gold-band { top: 267px; }
  .tube .gold-band { top: 482px; height: 3px; }

  .blush-body {
    position: absolute;
    left: 0; right: 0; bottom: 0;
    background:
      radial-gradient(ellipse at 10% 35%, var(--blush) 0%, transparent 45%),
      radial-gradient(ellipse at 95% 15%, var(--blush) 0%, transparent 35%),
      radial-gradient(ellipse at 80% 95%, var(--blush) 0%, transparent 45%),
      radial-gradient(ellipse at 15% 90%, var(--blush-soft) 0%, transparent 45%),
      #fdf8f7;
  }
  .carton .blush-body { top: 271px; }
  .tube .blush-body {
    top: 485px;
    background:
      radial-gradient(ellipse at 50% 100%, var(--blush) 0%, transparent 30%),
      linear-gradient(90deg, #ebe9e9, var(--tube-white) 35%, #ffffff 60%, #e7e5e5);
  }

  .brand-name {
    position: absolute;
    writing-mode: vertical-rl;
    transform: rotate(180deg);
    font-weight: 400;
    white-space: nowrap;
    line-height: 1;
    color: var(--ink);
  }
  .carton .brand-name { left: 155px; top: 320px; height: 382px; font-size: 76px; text-align: center; }
  .tube .brand-name { left: 49px; top: 518px; height: 270px; font-size: 46px; text-align: center; }

  .product-name {
    position: absolute;
    left: 0; width: 100%;
    text-align: center;
    font-weight: 500;
  }
  .carton .product-name { top: 758px; font-size: 26px; line-height: 31px; }
  .tube .product-name { top: 825px; font-size: 17px; line-height: 21px; font-weight: 400; }

  .volume {
    position: absolute;
    left: 0; width: 100%;
    text-align: center;
    font-weight: 500;
  }
  .carton .volume { top: 885px; font-size: 36px; }
  .tube .volume { top: 915px; font-size: 24px; color: #333; }
</style>
</head>
<body>
<main class="canvas">
  <section class="carton">
    <div class="floral-field" role="img" aria-label="Blush line-art floral pattern of peonies, lilies and leaves"></div>
    <div class="gold-band"></div>
    <div class="blush-body" role="img" aria-label="Soft blush pink watercolour wash">
    </div>
    <h1 class="brand-name">VelaMira</h1>
    <p class="product-name">Eyebrow<br>Growth Serum</p>
    <p class="volume">5ml</p>
  </section>

  <section class="tube">
    <div class="tube-cap"></div>
    <div class="floral-field" role="img" aria-label="Blush line-art floral pattern of peonies, lilies and leaves"></div>
    <div class="gold-band"></div>
    <div class="blush-body" role="img" aria-label="White label with faint blush watercolour wash"></div>
    <p class="brand-name">VelaMira</p>
    <p class="product-name">Eyebrow<br>Growth Serum</p>
    <p class="volume">5ml</p>
  </section>
</main>
</body>
</html>
```